Business Card - Tidal Lanes

Need Business Card design for company named Tidal Lanes. Software development focused mainly on Brindle Orvix & Zelt Apps. I've attached our logo with both a black and white background. Please add trademark symbol to logo when using.

```html
<!DOCTYPE html>
<html lang="en">
<head>
<meta charset="utf-8">
<title>Tidal Lanes — Business Card</title>
<link href="https://fonts.googleapis.com/css2?family=Open+Sans:wght@400;600;700&display=swap" rel="stylesheet">
<style>
  :root {
    --page: #e9e6e1;
    --card-dark: #1c1c1c;
    --card-mid: #2c2c2c;
    --band-orange: #f7952e;
    --rule-red: #d6231c;
    --name-yellow: #ffd21f;
    --text-white: #ffffff;
    --text-soft: #d9d9d9;
    --mark-orange: #f7941d;
  }
  * { box-sizing: border-box; margin: 0; padding: 0; }
  html, body {
    width: 1200px; height: 720px; overflow: hidden;
    background: var(--page);
    font-family: "Open Sans", Arial, sans-serif;
  }
  .stage {
    width: 1200px; height: 720px;
    display: flex; align-items: center; justify-content: center; gap: 40px;
  }
  .card {
    position: relative;
    width: 540px; height: 309px;
    border-radius: 3px;
    overflow: hidden;
    background:
      radial-gradient(ellipse at 50% 35%, var(--card-mid) 0%, var(--card-dark) 75%);
    box-shadow: 0 8px 24px rgba(0,0,0,.25);
    color: var(--text-white);
  }
  .brand {
    display: flex; align-items: center; justify-content: center; gap: 10px;
    font-weight: 700; color: var(--text-white); letter-spacing: -0.5px;
  }
  .brand-dot {
    border-radius: 50%; background: var(--mark-orange); flex: none;
  }

  /* Front */
  .card-front .brand { position: absolute; top: 52px; left: 0; right: 0; font-size: 30px; }
  .card-front .brand-dot { width: 20px; height: 20px; }
  .contact-band {
    position: absolute; left: 0; right: 0; top: 132px; height: 140px;
    background: var(--band-orange);
    border-top: 2px solid var(--rule-red);
    border-bottom: 2px solid var(--rule-red);
  }
  .person {
    text-align: center; margin-top: 12px; font-size: 17px; color: var(--text-white);
  }
  .person-name { color: var(--name-yellow); font-weight: 700; }
  .contact-row {
    display: flex; justify-content: center; align-items: center; margin-top: 22px;
    font-size: 14px; line-height: 1.55; color: var(--text-white);
  }
  .address { padding-right: 18px; text-align: left; }
  .divider { width: 1px; height: 46px; background: rgba(255,255,255,.7); }
  .phones { padding-left: 18px; }
  .phone { display: flex; align-items: center; gap: 7px; }
  .phone svg { width: 11px; height: 11px; fill: var(--text-white); }

  /* Back */
  .card-back .brand { position: absolute; top: 110px; left: 0; right: 0; font-size: 38px; }
  .card-back .brand-dot { width: 24px; height: 24px; }
  .website {
    position: absolute; top: 205px; left: 0; right: 0; text-align: center;
    font-size: 15px; letter-spacing: 3px; color: var(--text-soft);
  }
</style>
</head>
<body>
<main class="stage">
  <section class="card card-front" aria-label="Card front">
    <div class="brand"><span class="brand-dot"></span>Tidal Lanes</div>
    <div class="contact-band">
      <p class="person"><span class="person-name">Your Name,</span> Title</p>
      <div class="contact-row">
        <address class="address" style="font-style:normal">4210 Harbor Row<br>Marlow, FL 33990</address>
        <span class="divider"></span>
        <div class="phones">
          <p class="phone">
            <svg viewBox="0 0 12 12" aria-hidden="true"><rect x="3" y="0" width="6" height="12" rx="1"/></svg>
            555-214-7730
          </p>
          <p class="phone">
            <svg viewBox="0 0 12 12" aria-hidden="true"><path d="M1 4c0-2 10-2 10 0v1H8V4H4v1H1zM3 6h6l2 5H1z"/></svg>
            555-648-1092
          </p>
        </div>
      </div>
    </div>
  </section>

  <section class="card card-back" aria-label="Card back">
    <div class="brand"><span class="brand-dot"></span>Tidal Lanes</div>
    <p class="website">www.tidallanes.com</p>
  </section>
</main>
</body>
</html>
```